Super elegant, crisp & clean Business card design required

We recently upgraded our branding - which is on our website - talvendoraphoto.com

I would like a simple, yet elegant, clean business card design please.

The font of my logo is Cinzel - and because of the natural colour - it's best to have this on a black background.

I would like to have the back of the business card - with simply my logo.

PLEASE DO NOT SUBMIT A COMPLICATED / UNCLEAN DESIGN

Industry/Entity Type

Business

Contact Information for Business Card

Talven Doroshko Photography

Font styles to use
Other font styles liked:
• Cinzel

Requirements
Must have
• A backpage with nothing but my logo
• Simple design - stands out
Should not have
• Colour that dont align with my logo
• Over complicated '/ non symmetrical design

```html
<!DOCTYPE html>
<html lang="en">
<head>
<meta charset="utf-8">
<title>Talven Doroshko Photography – Business Card</title>
<link rel="stylesheet" href="https://fonts.googleapis.com/css2?family=Cinzel:wght@400&family=Source+Sans+3:wght@400&display=swap">
<style>
  :root{
    --stage:#c6c6c6;
    --card-dark:#141414;
    --card-tan:#85785b;
    --gold:#8f7d5b;
    --gold-light:#a08c68;
    --white:#ffffff;
    --cream:#f3ede2;
  }
  *{margin:0;padding:0;box-sizing:border-box}
  html,body{width:1200px;height:900px;overflow:hidden;background:var(--stage)}
  .stage{position:relative;width:1200px;height:900px}
  .card{position:absolute;top:200px;height:501px}
  .card-front{left:265px;width:310px;background:var(--card-dark);border-radius:50px 0 50px 0}
  .card-back{left:641px;width:309px;background:var(--card-tan);border-radius:50px 50px 0 50px}

  .brand{position:absolute;left:0;right:0;text-align:center;font-family:"Cinzel",serif;font-weight:400}
  .brand-mark{position:absolute;left:110px;top:60px;width:90px;height:90px;border:1.5px solid var(--gold);border-radius:50%}
  .brand-name{font-size:21px;letter-spacing:.5px;line-height:1}
  .brand-sub{font-size:10px;letter-spacing:6.5px;line-height:1;margin-top:5px;padding-left:6px}
  .card-front .brand{top:179px;color:var(--gold)}
  .card-back .brand{top:421px;color:var(--cream)}

  .contact{position:absolute;left:33px;top:287px;font-family:"Source Sans 3",sans-serif;color:var(--white)}
  .person-name{font-size:18px;color:var(--gold-light);line-height:20px}
  .person-role{font-size:14px;line-height:18px}
  .address{margin-top:19px;font-size:13.5px;line-height:15.5px}
  .lines{list-style:none;margin-top:15px}
  .lines li{display:flex;align-items:center;font-size:13.5px;line-height:21px}
  .lines svg{width:10px;height:10px;margin-right:9px;margin-left:1px;fill:var(--gold)}
</style>
</head>
<body>
<main class="stage">
  <section class="card card-front">
    <span class="brand-mark"></span>
    <div class="brand">
      <div class="brand-name">Talven Doroshko</div>
      <div class="brand-sub">PHOTOGRAPHY</div>
    </div>
    <div class="contact">
      <p class="person-name">Renata Vell</p>
      <p class="person-role">Managing Director</p>
      <p class="address">12345, Address Goes Here<br>Country Name, 123456</p>
      <ul class="lines">
        <li><svg viewBox="0 0 10 10"><path d="M2 0.5 3.6 2.6 2.7 3.8C3.3 5.2 4.7 6.6 6.2 7.3L7.4 6.4 9.5 8 8.4 9.5C4.5 9.3 0.7 5.5 0.5 1.6Z"/></svg>(044)-555-0182</li>
        <li><svg viewBox="0 0 10 10"><path d="M3.5 1h3v1.5h2.5v7h-8v-7h2.5Zm1 1v.5h1V2Z"/></svg>123-555-0147</li>
        <li><svg viewBox="0 0 10 10"><path d="M0.5 2h9v.6L5 5.6.5 2.6Zm0 1.6L5 6.6l4.5-3V8h-9Z"/></svg>hello@talvendoraphoto.com</li>
        <li><svg viewBox="0 0 10 10"><circle cx="5" cy="5" r="4.5"/></svg>www.talvendoraphoto.com</li>
      </ul>
    </div>
  </section>

  <section class="card card-back">
    <div class="brand">
      <div class="brand-name">Talven Doroshko</div>
      <div class="brand-sub">PHOTOGRAPHY</div>
    </div>
  </section>
</main>
</body>
</html>
```